Lucky Harbour Fun Casino Entertainment

Looking to update my business card and make it look more modern, stand out and eye catching.
We are are fun casino business in Australia (primarily Sydney). Blackjack and Roulette are our most popular games although we have pretty much every game available for hire that you would find in a real casino. The final design would need to be sleek and appeal to the more upmarket corporate sector.
We mainly cater for Corporate Events, Private Parties, Fundraising Events, Team Building, Poker Tournaments
I think I'd prefer the colour Black.

Target Market(s)

High-end Corporate

Industry/Entity Type

Events

Contact Information for Business Card

Rob Kendall
Director
1300 482 617
0433 728 591
info@luckyharbour.com.au
www.luckyharbour.com.au
Facebook & Instagram @luckyharbourevents (proper social icons preferred)

Colors
000000
0255a3

Requirements
Must have
• Front side:
• Logo
• Contact details
• 'Australia's #1 Fun Casino Specialists'
• Back:
• Logo
Nice to have
• Back:
• Corporate Events
• Private Parties
• Poker Tournaments
• Fundraising
• Props & Theming
• Photo Booth
• Horse Racing Events
• The Vegas Sign attached, maybe on the back of the card in the background...?

```html
<!DOCTYPE html>
<html lang="en">
<head>
<meta charset="utf-8">
<title>Lucky Harbour Fun Casino Entertainment – Business Card</title>
<link rel="stylesheet" href="https://fonts.googleapis.com/css2?family=Lato:wght@700&family=Open+Sans:wght@400&display=swap">
<style>
  :root {
    --backdrop: #7d4c22;
    --card: #040407;
    --gold: #f5a623;
    --text-light: #d2d2d2;
    --text-muted: #b9b9b9;
    --rule: #5a5a5a;
    --social-a: #3a5ea8;
    --social-b: #2a6aa3;
    --badge: #1c1c1f;
  }
  * { margin: 0; padding: 0; box-sizing: border-box; }
  html, body { width: 1200px; height: 900px; overflow: hidden; }
  body {
    position: relative;
    background: var(--backdrop);
    font-family: "Open Sans", Arial, sans-serif;
  }
  .card {
    position: absolute;
    background: var(--card);
    box-shadow: 2px 3px 6px rgba(0,0,0,.45);
    text-align: center;
  }
  .card--contact { left: 329px; top: 90px; width: 556px; height: 345px; }
  .card--brand   { left: 329px; top: 469px; width: 561px; height: 345px; }

  .contact__name {
    position: absolute; left: 0; right: 0; top: 62px;
    font-family: "Lato", Arial, sans-serif; font-weight: 700;
    font-size: 23px; color: var(--gold); letter-spacing: .2px;
  }
  .contact__role {
    position: absolute; left: 0; right: 0; top: 87px;
    font-size: 15px; color: var(--text-muted);
  }
  .divider {
    position: absolute; left: 192px; width: 171px; height: 24px;
    display: flex; align-items: center; justify-content: center; gap: 4px;
  }
  .divider::before, .divider::after {
    content: ""; flex: 1; height: 1px; background: var(--rule);
  }
  .divider::before { margin-right: 4px; }
  .divider::after { margin-left: 4px; }
  .divider--contact { top: 119px; }
  .divider--social { top: 232px; }
  .icon {
    width: 22px; height: 22px; border-radius: 50%;
    background: var(--gold);
    display: flex; align-items: center; justify-content: center;
  }
  .icon svg { width: 14px; height: 14px; }
  .social-dot { width: 22px; height: 22px; border-radius: 50%; background: var(--social-a); }
  .social-dot--alt { background: var(--social-b); }
  .contact__lines {
    position: absolute; left: 0; right: 0; top: 144px;
    list-style: none; font-size: 16px; line-height: 20.3px; color: var(--text-light);
  }
  .contact__handle {
    position: absolute; left: 0; right: 0; top: 255px;
    font-size: 16px; color: var(--text-light);
  }

  .brand__mark {
    position: absolute; left: 205px; top: 94px; width: 150px; height: 150px;
    border-radius: 50%; background: var(--badge);
  }
  .brand__name {
    position: absolute; left: 0; right: 0; top: 154px;
    font-family: "Lato", Arial, sans-serif; font-weight: 700;
    font-size: 30px; color: var(--gold); letter-spacing: .5px;
  }
  .brand__tagline {
    position: absolute; left: 0; right: 0; top: 286px;
    font-size: 16px; color: var(--gold); letter-spacing: .2px;
  }
</style>
</head>
<body>

<section class="card card--contact">
  <h1 class="contact__name">ROB KENDALL</h1>
  <p class="contact__role">Director</p>

  <div class="divider divider--contact">
    <span class="icon" aria-label="Phone">
      <svg viewBox="0 0 16 16"><path fill="#111" d="M2 6c0-2 2-3 6-3s6 1 6 3v1h-3V6H5v1H2zM4 8h8l1 5H3z"/><circle cx="8" cy="10.5" r="1.3" fill="#f5a623"/></svg>
    </span>
    <span class="icon" aria-label="Mobile">
      <svg viewBox="0 0 16 16"><rect x="4" y="1" width="8" height="14" rx="1.5" fill="#111"/><rect x="5.3" y="3" width="5.4" height="8" fill="#f5a623"/></svg>
    </span>
    <span class="icon" aria-label="Email">
      <svg viewBox="0 0 16 16"><rect x="1.5" y="3.5" width="13" height="9" fill="none" stroke="#111" stroke-width="1.6"/><path d="M1.5 3.5 8 9l6.5-5.5" fill="none" stroke="#111" stroke-width="1.6"/></svg>
    </span>
    <span class="icon" aria-label="Website">
      <svg viewBox="0 0 16 16"><circle cx="8" cy="8" r="6.3" fill="none" stroke="#111" stroke-width="1.6"/><path d="M5 4.5c2 1 1 3 3 3.5s1 3 2.5 3.5M9.5 2.5c0 1.5 2 1.5 3 2.5" fill="none" stroke="#111" stroke-width="1.4"/></svg>
    </span>
  </div>

  <ul class="contact__lines">
    <li>1300 482 617</li>
    <li>0433 728 591</li>
    <li>info@luckyharbour.com.au</li>
    <li>www.luckyharbour.com.au</li>
  </ul>

  <div class="divider divider--social">
    <span class="social-dot" aria-label="Social profile"></span>
    <span class="social-dot social-dot--alt" aria-label="Social profile"></span>
  </div>
  <p class="contact__handle">@luckyharbourevents</p>
</section>

<section class="card card--brand">
  <div class="brand__mark" aria-hidden="true"></div>
  <p class="brand__name">LUCKY HARBOUR</p>
  <p class="brand__tagline">AUSTRALIA'S #1 FUN CASINO SPECIALISTS</p>
</section>

</body>
</html>
```